Flyer to advertise gutter cleaning throughout the Autumn and winter monthss

I need a new flyer to advertise gutter and driveway cleaning, roof and gutter repairs.

I am an experienced licensed Plumber and Gasfitter looking to broaden my scope of work to gutter cleaning. I am experienced in cleaning gutter and live in a area with large gum trees. I wont something that's clear, eye catching but not too busy.

Flyer requirements: Free roof inspection - no obligation. Gutter Cleaning from $199. Pictures of men using blower or hands to clean roof gutters (no obvious faces) to be included. Australian looking houses.

A mention that 'All general plumbing maintenance' is offered as other services but not too much wording about this as the target is for gutter cleaning.

Phone number: 0427 385 912 (in this format)
Business Name: Larkvale Plumbing & Gasfitting
License: 3175420
ABN: 71364058227
Web: http://larkvaleplumbing.example.site/

Target Market(s)

Elderly - busy working class

Industry/Entity Type

Plumber

Font styles to use
Sans Serif

Colors
0355a3
fbed22
ec1f27
f78f20

Requirements
Must have
• Roof Gutter Cleaning pictures
• Men in protective clothing if possible
Nice to have
• More information:
• Prevent against flooding, mold, rust, rotting and corrosion now!
• Gutter Cleaning Services
• • Remove leaves, sticks, and other debris
• • Clear away clogs
• • Test your downpipes
• • Pinpoint any gutter issues
• • Repair gutter
• With regular service, you can count on your property to be well-protected no matter what the forecast!
Should not have
• Houses that don't look Australian

```html
<!DOCTYPE html>
<html lang="en">
<head>
<meta charset="utf-8">
<title>Larkvale Plumbing &amp; Gasfitting – Gutter Cleaning</title>
<link rel="stylesheet" href="https://fonts.googleapis.com/css2?family=Open+Sans:ital,wght@0,400;0,600;0,700;0,800;1,600;1,700&family=Dancing+Script:wght@600&display=swap">
<style>
  :root {
    --navy: #2b2463;
    --red: #e41e3a;
    --red-light: #ec2f5a;
    --yellow: #dccd3c;
    --teal: #137a74;
    --paper: #e6e6e6;
    --ink: #1a1a1a;
    --ink-grey: #666666;
    --white: #ffffff;
  }
  * { margin: 0; padding: 0; box-sizing: border-box; }
  html, body { width: 856px; height: 1200px; overflow: hidden; background: var(--paper); }
  .flyer {
    position: relative; width: 856px; height: 1200px; overflow: hidden;
    background: var(--paper);
    font-family: "Open Sans", Arial, sans-serif;
  }
  .hero-photo {
    position: absolute; left: 525px; top: 0; width: 331px; height: 724px;
    background: linear-gradient(180deg, #7f8fa8 0%, #4e5d78 35%, #3a4763 60%, #c98a3a 82%, #e7b43a 100%);
  }
  .backdrop-photo {
    position: absolute; left: 459px; top: 724px; width: 397px; height: 476px;
    background: linear-gradient(180deg, #b9bcc0 0%, #8f9397 60%, #4a4a48 100%);
  }
  .navy-panel {
    position: absolute; left: 0; top: 0; width: 525px; height: 503px;
    background: var(--navy);
  }
  .brand { position: absolute; left: 61px; top: 66px; display: flex; align-items: center; gap: 10px; }
  .brand-dot { width: 54px; height: 54px; border-radius: 50%; background: var(--red); }
  .brand-name { color: var(--white); font-weight: 700; font-size: 14px; line-height: 1.2; width: 170px; }
  .accent-rule { position: absolute; left: 61px; top: 157px; width: 135px; height: 3px; background: var(--red); }
  .headline {
    position: absolute; left: 56px; top: 178px;
    color: var(--white); font-weight: 800; font-size: 86px; line-height: 90px; letter-spacing: 1px;
  }
  .price { position: absolute; left: 60px; top: 356px; display: flex; align-items: baseline; gap: 22px; }
  .price-from { font-family: "Dancing Script", cursive; color: var(--white); font-size: 62px; }
  .price-amount { color: var(--yellow); font-weight: 800; font-size: 78px; }
  .warning-band {
    position: absolute; left: 0; top: 503px; width: 525px; height: 151px;
    background: linear-gradient(90deg, var(--red) 0%, var(--red-light) 100%);
  }
  .warning-text {
    position: absolute; left: 63px; top: 530px; width: 310px;
    color: var(--white); font-style: italic; font-weight: 600; font-size: 20.5px; line-height: 31px;
  }
  .guarantee-seal {
    position: absolute; left: 388px; top: 442px; width: 258px; height: 258px;
    border-radius: 50%; background: var(--teal); border: 4px solid var(--white);
  }
  .services { position: absolute; left: 44px; top: 700px; }
  .services-title { color: var(--navy); font-weight: 800; font-size: 26.5px; letter-spacing: 0.3px; }
  .services-list { list-style: none; margin-top: 8px; }
  .services-list li {
    position: relative; padding-left: 26px; color: var(--ink); font-size: 18.5px; font-weight: 600; line-height: 31px;
  }
  .services-list li svg { position: absolute; left: 2px; top: 11px; }
  .services-note {
    position: absolute; left: 47px; top: 905px; width: 360px;
    color: var(--ink); font-style: italic; font-weight: 700; font-size: 13px; line-height: 17px;
  }
  .extra-services {
    position: absolute; left: 47px; top: 946px; width: 380px;
    color: var(--red); font-weight: 700; font-size: 13px; line-height: 17px;
  }
  .contact { position: absolute; left: 0; top: 983px; width: 472px; text-align: center; }
  .offer { color: var(--navy); font-weight: 800; font-size: 25px; line-height: 30px; letter-spacing: 0.5px; }
  .phone { color: var(--red); font-weight: 800; font-size: 52px; line-height: 60px; margin-top: 8px; }
  .web { color: var(--navy); font-weight: 700; font-size: 14px; margin-top: 2px; }
  .legal { color: var(--ink-grey); font-size: 12.5px; margin-top: 2px; }
  .work-photo {
    position: absolute; left: 459px; width: 397px; border: 8px solid var(--white); border-right: none;
  }
  .work-photo--hands { top: 727px; height: 174px; background: linear-gradient(135deg, #6e8a4a 0%, #b98a52 45%, #6c6661 100%); }
  .work-photo--gutter { top: 916px; height: 174px; background: linear-gradient(180deg, #c5c8cc 0%, #9b7f6e 40%, #7d8185 70%, #a3a6a9 100%); }
  .licence-tag {
    position: absolute; left: 459px; top: 1108px; width: 397px; text-align: center;
    color: var(--white); font-weight: 800; font-size: 21px; line-height: 30px;
  }
</style>
</head>
<body>
<main class="flyer">
  <div class="hero-photo" role="img" aria-label="Close-up of roof shingles with autumn leaves in a gutter"></div>
  <div class="backdrop-photo" role="img" aria-label="Blurred roof and gutter background"></div>

  <section class="navy-panel">
    <div class="brand">
      <span class="brand-dot"></span>
      <span class="brand-name">LARKVALE PLUMBING &amp; GASFITTING</span>
    </div>
    <div class="accent-rule"></div>
    <h1 class="headline">GUTTER<br>CLEANING</h1>
    <p class="price"><span class="price-from">From</span><span class="price-amount">$199</span></p>
  </section>

  <div class="warning-band"></div>
  <p class="warning-text">Prevent against flooding, mold, rust, rotting and corrosion by CALLING US TODAY!</p>

  <div class="guarantee-seal" role="img" aria-label="All work guaranteed seal"></div>

  <section class="services">
    <h2 class="services-title">GUTTER CLEANING SERVICES</h2>
    <ul class="services-list">
      <li><svg width="14" height="11" viewBox="0 0 14 11"><path d="M1 6 L5 10 L13 1" fill="none" stroke="#e41e3a" stroke-width="2"/></svg>Remove leaves, sticks, and other debris</li>
      <li><svg width="14" height="11" viewBox="0 0 14 11"><path d="M1 6 L5 10 L13 1" fill="none" stroke="#e41e3a" stroke-width="2"/></svg>Test downpipes</li>
      <li><svg width="14" height="11" viewBox="0 0 14 11"><path d="M1 6 L5 10 L13 1" fill="none" stroke="#e41e3a" stroke-width="2"/></svg>Pinpoint any gutter issues</li>
      <li><svg width="14" height="11" viewBox="0 0 14 11"><path d="M1 6 L5 10 L13 1" fill="none" stroke="#e41e3a" stroke-width="2"/></svg>Repair gutters</li>
      <li><svg width="14" height="11" viewBox="0 0 14 11"><path d="M1 6 L5 10 L13 1" fill="none" stroke="#e41e3a" stroke-width="2"/></svg>New Installation</li>
    </ul>
  </section>
  <p class="services-note">With regular service, you can count on your property to be well-protected no matter what the forecast!</p>
  <p class="extra-services">Also offering all general plumbing maintenance.</p>

  <section class="contact">
    <p class="offer">FREE ROOF INSPECTION<br>NO OBLIGATION</p>
    <p class="phone">0427 385 912</p>
    <p class="web">larkvaleplumbing.example.site</p>
    <p class="legal">License: 3175420 | ABN: 71364058227</p>
  </section>

  <div class="work-photo work-photo--hands" role="img" aria-label="Gloved hand scooping dry leaves out of a roof gutter"></div>
  <div class="work-photo work-photo--gutter" role="img" aria-label="Roof gutter filled with gum nuts and debris"></div>
  <p class="licence-tag">Licensed Plumber,<br>Drainer &amp; Gasfitter</p>
</main>
</body>
</html>
```